Kelvaro.ch is looking for business card letterhead and envelope C5 with WOW effect

We need a strong business card for our company Kelvaro.ch, logo is available. You want a black or dark background on which the logo Stark r% 26 # 252; appears. Letterhead and envelope in C5 format should be in a similar design, but does not have to be We need a strong business card for our company Kelvaro.ch, logo is available. A black or dark background is desired, on which the logo Stark comes across. The letterhead and the envelope in C5 format should have a similar design.

Target Market(s)

Private customers as well as entrepreneurs

Contact Information for Business Card

E-mail: info@kelvaro-example.ch
Web.www.Kelvaro-example.ch
Tel: +41 ( 0 ) 79 482 6037
Adresse:
Lindenweg 14
9406 Tarnbach

Hier kann man Icons verwenden für Email,Tel und Adressse

Font styles to use
Other font styles liked:
• Dubai,bold

Colors

Designer to choose colors to be used in the design.

Requirements
Must have
• WOW effect
Nice to have
• R% 26 # 252; back business card with our service listings. - VEHICLE LABELING - SHOP WINDOW LABELING - STICKERS AND MUCH MORE ... in red color

```html
<!DOCTYPE html>
<html lang="en">
<head>
<meta charset="utf-8">
<title>Kelvaro.ch – Business Card</title>
<link rel="stylesheet" href="https://fonts.googleapis.com/css2?family=Arimo:wght@400&family=Open+Sans:wght@400;700&display=swap">
<style>
  :root {
    --page-bg: #e6e6e6;
    --card-dark: #070707;
    --card-light-top: #ffffff;
    --card-light-bottom: #ececec;
    --accent: #f7c600;
    --text-light: #ffffff;
    --text-dark: #141414;
    --divider: #3b3a12;
  }
  * { margin: 0; padding: 0; box-sizing: border-box; }
  html, body {
    width: 1200px; height: 900px; overflow: hidden;
    background: var(--page-bg);
  }
  .card {
    position: absolute; left: 100px; top: 140px;
    width: 1000px; height: 620px;
    background: linear-gradient(160deg, var(--card-light-top), var(--card-light-bottom));
    overflow: hidden;
    box-shadow: 0 12px 36px rgba(0,0,0,0.18);
  }
  .card__panel { position: absolute; inset: 0; }
  .contact {
    position: absolute; left: 58px; top: 0;
    font-family: "Arimo", Arial, sans-serif;
    font-size: 31px; color: var(--text-light);
  }
  .contact__row {
    position: absolute; left: 0; display: flex; align-items: center;
    white-space: nowrap; line-height: 1;
  }
  .contact__icon { width: 40px; height: 36px; margin-right: 14px; flex: none; }
  .contact__row--phone { top: 92px; }
  .contact__row--mail { top: 138px; }
  .contact__row--web { top: 183px; }
  .address {
    position: absolute; left: 0; top: 267px; display: flex; align-items: flex-start;
  }
  .address__lines { line-height: 39px; white-space: nowrap; margin-top: -2px; }
  .divider {
    position: absolute; left: 58px; top: 385px; width: 338px; height: 1px;
    background: var(--divider);
  }
  .services {
    position: absolute; left: 66px; top: 432px; list-style: none;
    font-family: "Open Sans", Arial, sans-serif; font-size: 25px;
    color: var(--text-light); text-transform: uppercase;
  }
  .services__item {
    display: flex; align-items: center; height: 45.5px; white-space: nowrap;
  }
  .services__item::before {
    content: ""; width: 14px; height: 14px; border-radius: 50%;
    background: var(--accent); margin-right: 12px; flex: none;
  }
  .brand {
    position: absolute; left: 566px; top: 268px;
    display: flex; align-items: center;
  }
  .brand__dot {
    width: 80px; height: 80px; border-radius: 50%;
    background: var(--accent); margin-right: 26px;
  }
  .brand__name {
    font-family: "Open Sans", Arial, sans-serif; font-weight: 700;
    font-size: 40px; color: var(--text-dark); letter-spacing: 1px;
  }
</style>
</head>
<body>
  <div class="card">
    <svg class="card__panel" viewBox="0 0 1000 620" width="1000" height="620" aria-hidden="true">
      <polygon points="0,0 641,0 440,310 641,620 0,620" fill="var(--card-dark)"/>
      <polyline points="641,0 440,310 641,620" fill="none" stroke="var(--accent)" stroke-width="4"/>
    </svg>

    <div class="contact">
      <div class="contact__row contact__row--phone">
        <svg class="contact__icon" viewBox="0 0 40 36" aria-hidden="true">
          <rect x="2" y="1" width="34" height="34" rx="5" fill="none" stroke="var(--accent)" stroke-width="3"/>
          <path d="M12 9c2-1 3 0 4 3l1 2c0 1-1 2-2 3 1 3 3 5 6 6 1-1 2-2 3-2l2 1c3 1 4 2 3 4-1 2-3 3-5 2-7-2-12-7-14-14-1-2 0-4 2-5z" fill="var(--accent)"/>
        </svg>
        <span>+41 ( 0 ) 79 482 6037</span>
      </div>
      <div class="contact__row contact__row--mail">
        <svg class="contact__icon" viewBox="0 0 40 36" aria-hidden="true">
          <rect x="1" y="7" width="38" height="24" rx="2" fill="var(--accent)"/>
          <polyline points="2,9 20,22 38,9" fill="none" stroke="var(--card-dark)" stroke-width="2.5"/>
        </svg>
        <span>info@kelvaro-example.ch</span>
      </div>
      <div class="contact__row contact__row--web">
        <svg class="contact__icon" viewBox="0 0 40 36" aria-hidden="true">
          <g fill="none" stroke="var(--accent)" stroke-width="2.5">
            <circle cx="20" cy="18" r="16"/>
            <ellipse cx="20" cy="18" rx="7" ry="16"/>
            <line x1="4" y1="18" x2="36" y2="18"/>
            <path d="M7 9h26M7 27h26"/>
          </g>
        </svg>
        <span>www.Kelvaro-example.ch</span>
      </div>
      <div class="address">
        <svg class="contact__icon" viewBox="0 0 40 54" style="height:52px" aria-hidden="true">
          <path d="M20 2C11 2 4 9 4 18c0 12 16 32 16 32s16-20 16-32C36 9 29 2 20 2z" fill="var(--accent)"/>
          <circle cx="20" cy="18" r="6" fill="var(--card-dark)"/>
        </svg>
        <div class="address__lines">
          <div>Lindenweg 14</div>
          <div>9406 Tarnbach</div>
        </div>
      </div>
    </div>

    <div class="divider"></div>

    <ul class="services">
      <li class="services__item">Vehicle labeling</li>
      <li class="services__item">Shop window labeling</li>
      <li class="services__item">Stickers and much more ...</li>
    </ul>

    <div class="brand">
      <div class="brand__dot"></div>
      <span class="brand__name">KELVARO.CH</span>
    </div>
  </div>
</body>
</html>
```